Business Card Design for Vintage Jazz

I am a vintage jazz band leader in New York City. My groups play the music of the 1920s, 1930s and 1940s. My website is morvalquist.com for more info on what I do.

I am looking for a two sided business card design that has the look and feel of a really nice business card from the 1930s. I need to convey with the design that my work has that vintage kind of class and style, but also conveys that we are fun and entertaining.

Most importantly it should make a bold staement. If Hal Denbrook had a card, what would it have looked like? I want a card that I feel confident will make an impact and will let people know that my work is te the top that NYC has to offer in vintage jazz..

Note that I have only decided to avoid the "committed payment" option as I have not used this service before. Assuming that I get quality work I will select a design from those presented.

Target Market(s)

people who want to hire my band for events, media, and new fans of the band

Industry/Entity Type

Performing Art

Contact Information for Business Card

Definitely a matte finish, possibly a sort of old style of paper with that brown tint? definitely a thick card.

Requirements
Must have
• FRONT
• My name: Tobin Vashley
• What I do: Bandleader, Guitarist, Vocalist, Songwriter
• Contact Details: morvalquist.com tobin@morvalquist.com 646-555-0148
• BACK
• My Social Media Links:
• facebook.morvalquist.com
• twitter, instagram, linkedin: morvalquist
• I'm also including a photo image I would like to use. The photo's background is not needed, and to be honest isn't really desireable. Just looking to use the image of me.
Nice to have
• I'm attaching which could be used as is, omitted from the card, or altered maybe with text going around the outside of the circle or in some other way. It may need some clean up to the edges of the lettering as we only use it for the website thumbnail.
• If there's space I'd like to include the text "join our mailing list for a free song download: freesong.morvalquist.com" If not perhaps just "Download a Free Song at: freesong.morvalquist.com - something to this end.
Should not have
• anything cartoony. Don't think retro 90s's vision of the swing era, think actual swing era!
• anything modern. Got to look old school
• Try to avoid dark backgrounds. Since we often play in bars and clubs where it is dar, a d
• avoid script fonts.

```html
<!DOCTYPE html>
<html lang="en">
<head>
<meta charset="utf-8">
<title>Tobin Vashley — Business Card</title>
<link rel="stylesheet" href="https://fonts.googleapis.com/css2?family=Open+Sans:wght@400;700&display=swap">
<style>
  :root {
    --ink: #0d0d0d;
    --paper: #ffffff;
    --backdrop: #e4e2de;
    --back-text: #f2f2f2;
    --card-shadow: rgba(0,0,0,0.18);
  }
  * { margin: 0; padding: 0; box-sizing: border-box; }
  html, body {
    width: 1200px; height: 900px; overflow: hidden;
    background: var(--backdrop);
    font-family: "Open Sans", sans-serif;
  }
  .card {
    position: absolute; left: 250px;
    width: 700px; height: 400px;
    box-shadow: 0 6px 18px var(--card-shadow);
    overflow: hidden;
  }

  /* Back side */
  .card--back { top: 40px; background: var(--ink); color: var(--back-text); }
  .social-list {
    position: absolute; left: 120px; top: 140px;
    list-style: none; font-size: 23px; line-height: 34px;
  }
  .social-list li { display: flex; align-items: center; gap: 14px; }
  .social-marker {
    width: 13px; height: 13px; background: var(--back-text);
    flex: none;
  }

  .monogram {
    position: absolute; display: flex; flex-direction: column;
    align-items: center; gap: 12px;
  }
  .monogram__circle {
    width: 110px; height: 110px; border-radius: 50%;
    border: 4px solid currentColor;
  }
  .monogram__name { font-size: 20px; font-weight: 400; letter-spacing: 1px; }
  .card--back .monogram { right: 80px; top: 120px; color: var(--back-text); }

  /* Front side */
  .card--front { top: 460px; background: var(--paper); color: var(--ink); }
  .corner-mark { position: absolute; left: 24px; top: 0; }
  .name {
    position: absolute; left: 96px; top: 30px;
    font-size: 29px; font-weight: 700; line-height: 1;
  }
  .contact-list {
    position: absolute; left: 40px; top: 196px;
    list-style: none; font-size: 18px; line-height: 25px;
  }
  .contact-list li { display: flex; align-items: center; gap: 10px; }
  .contact-list svg { width: 13px; height: 13px; flex: none; }
  .role {
    position: absolute; left: 40px; top: 286px;
    font-size: 19px; line-height: 1.2;
  }
  .bottom-band { position: absolute; left: 0; bottom: 0; }
  .card--front .monogram { right: 90px; top: 100px; color: var(--ink); }
</style>
</head>
<body>

<section class="card card--back" aria-label="Card back">
  <ul class="social-list">
    <li><span class="social-marker"></span>morvalquist.com</li>
    <li><span class="social-marker"></span>morvalquist</li>
    <li><span class="social-marker"></span>morvalquist</li>
    <li><span class="social-marker"></span>morvalquist</li>
  </ul>
  <div class="monogram">
    <div class="monogram__circle"></div>
    <span class="monogram__name">Morvalquist</span>
  </div>
</section>

<section class="card card--front" aria-label="Card front">
  <svg class="corner-mark" width="56" height="42" viewBox="0 0 56 42">
    <rect width="56" height="42" fill="var(--ink)"/>
    <polygon points="50,3 55,3 13,40 8,40" fill="var(--paper)"/>
  </svg>
  <h1 class="name">Tobin Vashley</h1>

  <ul class="contact-list">
    <li>
      <svg viewBox="0 0 16 16"><path d="M3 1l3 3-1.5 2c1 2 3 4 5 5l2-1.5 3 3-2 2C7 14 2 9 1 3z" fill="var(--ink)"/></svg>
      646-555-0148
    </li>
    <li>
      <svg viewBox="0 0 16 16"><rect x="1" y="3" width="14" height="10" fill="var(--ink)"/><path d="M1 3l7 6 7-6" stroke="var(--paper)" stroke-width="1.4" fill="none"/></svg>
      tobin@morvalquist.com
    </li>
    <li>
      <svg viewBox="0 0 16 16"><circle cx="8" cy="8" r="7" fill="var(--ink)"/><path d="M1 8h14M8 1c-3 4-3 10 0 14M8 1c3 4 3 10 0 14" stroke="var(--paper)" stroke-width="1" fill="none"/></svg>
      morvalquist.com
    </li>
  </ul>
  <p class="role">Bandleader, Guitarist, Vocalist, Songwriter</p>

  <svg class="bottom-band" width="700" height="60" viewBox="0 0 700 60">
    <polygon points="0,22 28,22 28,60 0,60" fill="var(--ink)"/>
    <polygon points="28,50 270,50 266,60 28,60" fill="var(--ink)"/>
    <polygon points="290,30 700,30 700,60 278,60" fill="var(--ink)"/>
  </svg>

  <div class="monogram">
    <div class="monogram__circle"></div>
    <span class="monogram__name">Morvalquist</span>
  </div>
</section>

</body>
</html>
```